BuildLinkHub.com Full Stationery Design

Business Card will have all info on it. Letterhead will not have name, title or mobile number. Keep general feeling very clean, using colors from the logo as accents.
Name:Dale Marchetti
Title:President
Phone: 1-800-555-0142
Cell: 306-555-0187
email: dale@buildlinkhub.example
website: www.buildlinkhub.example
Address:
PO Box 947
Cedarholm, AB
S0J2T0

Target Market(s)

Construction Business owners

Industry/Entity Type

Business

Contact Information for Business Card

Name:Dale Marchetti
Title:President
Phone: 1-800-555-0142
Cell: 306-555-0187
Address:
PO Box 947
Cedarholm, AB
S0J2T0

Font styles to use
Sans Serif

Requirements
Must have
• Clean look
Should not have
• Images or cartoon type characters or tools

```html
<!DOCTYPE html>
<html lang="en">
<head>
<meta charset="utf-8">
<title>BuildLinkHub.com Business Card</title>
<link href="https://fonts.googleapis.com/css2?family=Source+Sans+3:wght@400;600&display=swap" rel="stylesheet">
<style>
  :root {
    --stage: #e9e7e3;
    --card-white: #ffffff;
    --slate: #4a5a6b;
    --slate-text: #4d5866;
    --body-text: #555a60;
    --accent: #f04e23;
    --on-dark: #ffffff;
  }
  * { margin: 0; padding: 0; box-sizing: border-box; }
  html, body {
    width: 1200px; height: 987px; overflow: hidden;
    background: var(--stage);
    font-family: "Source Sans 3", sans-serif;
  }
  .canvas { position: relative; width: 1200px; height: 987px; }
  .card {
    position: absolute; left: 293px; width: 615px; height: 352px;
    box-shadow: 0 2px 6px rgba(0,0,0,0.18);
  }
  .card-front { top: 130px; background: var(--card-white); }
  .card-back { top: 506px; background: var(--slate); }

  .brand-band {
    position: absolute; left: 0; top: 46px; width: 58px; height: 73px;
    background: var(--accent);
  }
  .brand-name {
    position: absolute; left: 80px; top: 64px;
    font-size: 30px; font-weight: 600; color: var(--slate-text);
    letter-spacing: 0.2px; white-space: nowrap;
  }

  .contact {
    position: absolute; left: 46px; top: 173px;
    list-style: none; font-size: 15.5px; color: var(--body-text); line-height: 23px;
  }
  .contact .address { margin-bottom: 5px; }
  .contact li { display: flex; align-items: center; white-space: nowrap; }
  .contact svg { width: 14px; height: 14px; margin-right: 9px; fill: var(--slate-text); flex: none; }

  .person { position: absolute; right: 49px; top: 218px; text-align: right; }
  .person-name { font-size: 22px; font-weight: 600; color: var(--slate-text); line-height: 26px; }
  .person-title { font-size: 16px; color: var(--accent); line-height: 22px; }

  .back-name {
    position: absolute; left: 0; right: 0; top: 152px; text-align: center;
    font-size: 34px; font-weight: 600; color: var(--on-dark);
  }
  .back-web {
    position: absolute; left: 0; right: 0; top: 290px; text-align: center;
    font-size: 16.5px; color: var(--on-dark);
  }
</style>
</head>
<body>
<main class="canvas">
  <section class="card card-front">
    <div class="brand-band"></div>
    <div class="brand-name">BuildLinkHub.com</div>

    <ul class="contact">
      <li class="address-line">PO Box 947</li>
      <li class="address-line address">Cedarholm, AB, S0J2T0</li>
      <li><svg viewBox="0 0 16 16"><path d="M3.6 1.2l2.3 2.6-1.3 2c.9 2 2.4 3.5 4.4 4.5l2-1.3 2.7 2.3-1.2 2.5C7.6 13.6 2.4 8.4 1.2 3z"/></svg>1-800-555-0142</li>
      <li><svg viewBox="0 0 16 16"><path d="M4 1h8v14H4zM5.5 2.5v9.5h5V2.5z"/></svg>306-555-0187</li>
      <li><svg viewBox="0 0 16 16"><path d="M1 3.5h14v9H1zm1.5 1.2v.3L8 8.6 13.5 5v-.3zM2.5 6.6v4.4h11V6.6L8 10.2z"/></svg>dale@buildlinkhub.example</li>
      <li><svg viewBox="0 0 16 16"><circle cx="8" cy="8" r="6.5"/></svg>www.buildlinkhub.example</li>
    </ul>

    <div class="person">
      <div class="person-name">Dale Marchetti</div>
      <div class="person-title">President</div>
    </div>
  </section>

  <section class="card card-back">
    <div class="back-name">BuildLinkHub.com</div>
    <div class="back-web">www.buildlinkhub.example</div>
  </section>
</main>
</body>
</html>
```